Flyer, poster, banner and social media titles designs for Community Mending Chartre

The Harbourline Charter for Community Mending provide a nationally agreed framework to guide recovery policy and practice across Australia. The Principles support recovery practitioners, governments, non-government organisations and communities to deliver effective, community-centred recovery outcomes.
The Principles have recently been refreshed through extensive consultation and we require a contemporary visual identity and design suite that will increase awareness, engagement and practical application of the Principles.
The redesign will cover:
• A4 Brochure (primary publication)
• A3 Poster
• Pull up banner
• Social Media Tiles
The new design should:
• Create a recognisable brand for the Harbourline Charter.
• Appeal to both experienced and emerging recovery practitioners.
• Reflect contemporary disaster recovery practice.
• Feel people-focused rather than government-focused.
• Support future resources such as videos, implementation guides, presentations and workshop materials.
• Remain relevant for several years without requiring a major redesign.
Target Audience
• Disaster recovery practitioners
• Government agencies
• Non-government organisations
• Community recovery workers
• Recovery managers and leaders
• Community stakeholders and volunteers
The visual identity should reflect the six Principles:
• Understanding Context
• Recognising Complexity
• Community-Centred Approaches
• Coordination
• Communication
• Capacity Building
The design should communicate:
• Recovery is centred on people and communities.
• Recovery is collaborative and involves many sectors.
• Recovery is adaptive, inclusive and evidence-informed.
• Recovery supports resilience and long-term wellbeing.
• The Principles provide practical guidance for recovery practice.
We are looking for:
• Modern and professional
• Warm and approachable
• Human-centred
• Inclusive and accessible
• Australian in context
• Visually engaging
• Suitable for print and digital use
We would like to avoid:
• Images of disaster destruction
• Emergency response imagery (fire trucks, flashing lights, etc.)
• Overly corporate or bureaucratic designs
• Designs that focus on deficits rather than recovery and growth
Consider themes such as:
• Connection and collaboration
• Communities and people
• Growth, recovery and renewal
Accessibility
Designs should:
• Meet accessibility best practice
• Use clear typography
• Achieve strong colour contrast
• Be suitable for both digital and print formats

Deliverables
1. Principles Brochure
• A4 trifold size x 2 (online and print friendly version)
• A side to include cover side, logos side and overview of principles.
• B side full details of the principles
• Graphic to highlight the 3 c’s concept (RECOVERY Context, complexity, community centred, coordinate, communicate and capacity). Currently 3 circles.
• Can be printed and distributed electronically
2. Poster
• A1 and A3 versions
• Suitable for office and workshop display
3. Pull-Up Banner - 850 mm (W) × 2000 mm (H)
• Conference and event use
• High visual impact
• Strong branding and concise messaging
4. Social Media Tiles x 3

We are providing an extension and increasing the budget following feedback from designers. We are wanting the resources to look and feel different from the existing designs, considering either a different colour palette in the designs or different motif with the leave design. Any nature based designs should consider the Australian fauna or flora. Also suggest avoiding images in the designs. The principles are not numbered or liner in the concept of how they function. Happy to answer any further questions and thank you for your suggested concepts.

Disaster recovery practitioners, Government agencies , Non-government organisations, Community recovery workers and Community stakeholders and volunteers

Disaster recovery

• Modern, warm, visually engaging, human-centred, Australian in context and different to the current design.
• Symbols for each principles
• Images of disaster destruction, Emergency response imagery, Overly corporate or bureaucratic designs, Designs that focus on deficits rather than recovery and growth, avoid too much black

```html
<!DOCTYPE html>
<html lang="en">
<head>
<meta charset="utf-8">
<title>Harbourline Charter for Community Mending – Design Suite</title>
<link href="https://fonts.googleapis.com/css2?family=Figtree:wght@400;500;600;700&display=swap" rel="stylesheet">
<style>
:root{
  --forest:#0e3a38;
  --navy:#0c2c44;
  --ink:#0c2e40;
  --cream:#f6f0e2;
  --leaf:#8db03f;
  --deep-leaf:#2e6a45;
  --c-context:#6c9a3a;
  --c-complex:#3f6a92;
  --c-community:#e0662a;
  --c-coordinate:#1f8f89;
  --c-communicate:#7d5a99;
  --c-capacity:#d3a82a;
  --white:#ffffff;
  --label:#1a1a1a;
}
*{box-sizing:border-box;margin:0;padding:0}
html,body{width:1200px;height:800px;overflow:hidden;background:var(--white);font-family:"Figtree",sans-serif;color:var(--label)}
.canvas{position:relative;width:1200px;height:800px}
.section-label{position:absolute;font-weight:700;font-size:13px;letter-spacing:.2px}
.section-label small{display:block;font-size:10px;font-weight:500}
.piece{position:absolute;overflow:hidden}
.art{position:absolute}
.hidden-defs{position:absolute;width:0;height:0}

/* brochure */
.brochure{left:17px;top:47px;width:546px;height:466px;display:flex}
.panel{position:relative;height:100%;overflow:hidden}
.panel-cover{width:197px;background:var(--forest);color:var(--white);padding:50px 0 0 20px}
.panel-partners{width:155px;background:var(--cream);padding:22px 10px 0}
.panel-overview{width:194px;background:var(--forest);color:var(--white);padding:30px 14px 0 20px}
.kicker{font-size:10px;font-weight:500;letter-spacing:.3px;text-transform:uppercase}
.title-a{font-weight:600;line-height:.95;letter-spacing:-.5px;color:var(--white)}
.title-b{font-weight:600;line-height:.95;letter-spacing:-.5px;color:var(--leaf)}
.cover-title .title-a,.cover-title .title-b{font-size:30px}
.cover-tagline{font-size:10px;line-height:1.45;margin-top:26px;width:105px}
.cover-values{position:absolute;left:20px;bottom:34px;font-size:9.5px;line-height:1.5;color:var(--leaf)}
.partners-heading{font-size:8px;font-weight:600;color:var(--deep-leaf);text-align:center;line-height:1.3;text-transform:uppercase}
.partner-list{display:grid;grid-template-columns:1fr 1fr;gap:13px 6px;margin-top:18px}
.partner{display:flex;align-items:center;gap:5px;font-size:6.5px;font-weight:600;color:var(--ink);line-height:1.2}
.partner.wide{grid-column:1 / span 2;padding-left:20px}
.partner-mark{width:16px;height:16px;border-radius:50%;background:#b7bfc2;flex:none}
.partner-mark.square{border-radius:2px}
.overview-text{font-size:7.6px;line-height:1.55;margin-bottom:9px}
.overview-heading{font-size:9px;font-weight:700;color:var(--leaf);margin:14px 0 8px}
.principle-row{display:flex;gap:8px;margin-bottom:9px;align-items:flex-start}
.principle-row .dot{width:22px;height:22px;flex:none}
.principle-row strong{display:block;font-size:7.2px;font-weight:700}
.principle-row span{display:block;font-size:6.4px;line-height:1.4;opacity:.85}

/* poster */
.poster{left:580px;top:49px;width:365px;height:657px;background:var(--cream)}
.poster-title{position:absolute;top:72px;left:0;width:100%;text-align:center}
.poster-title .kicker{font-size:14px;color:var(--ink)}
.poster-title .title-a{font-size:48px;color:var(--ink);margin-top:6px}
.poster-title .title-b{font-size:48px;color:var(--deep-leaf)}
.poster-tagline{position:absolute;top:200px;width:100%;text-align:center;font-size:11.5px;font-weight:600;line-height:1.4;color:var(--ink)}
.poster-diagram{position:absolute;left:32px;top:240px}
.poster-values{position:absolute;top:548px;width:100%;text-align:center;font-size:11.5px;font-weight:600;color:var(--ink)}
.poster-values i{font-style:normal;margin:0 6px}
.poster-wave{position:absolute;left:0;bottom:0;width:100%;height:80px}
.poster-sign{position:absolute;bottom:20px;width:100%;text-align:center;color:var(--white);font-size:11.5px}

/* banner */
.banner{left:961px;top:53px;width:215px;height:692px;background:var(--cream)}
.banner-head{position:absolute;left:0;top:0;width:100%;height:230px;background:var(--navy);padding:48px 0 0 22px;color:var(--white)}
.banner-head .kicker{font-size:11px}
.banner-head .title-a,.banner-head .title-b{font-size:33px}
.banner-tagline{font-size:10.5px;line-height:1.45;margin-top:14px;width:170px}
.banner-list{position:absolute;left:20px;top:264px}
.banner-item{display:flex;align-items:center;gap:12px;height:36px;margin-bottom:11px;font-size:10.5px;line-height:1.2;color:var(--ink)}
.banner-item svg{flex:none}
.banner-item b{font-weight:700}
.banner-foot{position:absolute;left:0;bottom:0;width:100%;height:130px;background:var(--navy);padding:48px 0 0 22px}
.banner-foot .values{font-size:9.5px;color:var(--leaf)}
.banner-foot .sign{font-size:10.5px;color:var(--white);line-height:1.4;margin-top:18px}

/* social */
.tile{top:557px;height:215px}
.tile-people{left:17px;width:171px;background:var(--forest);color:var(--white);padding:38px 0 0 15px}
.tile-guide{left:200px;width:182px;background:var(--cream);padding:50px 0 0 16px}
.tile-journey{left:393px;width:170px;background:var(--navy);color:var(--white);padding:40px 0 0 17px}
.tile-head{font-size:14px;font-weight:600;line-height:1.22}
.tile-body{font-size:9px;line-height:1.5;margin-top:12px}
.tile-guide .tile-head{font-size:16px;color:var(--ink)}
.tile-guide .tile-head span{color:var(--deep-leaf)}
.tile-guide .tile-body{width:88px;color:var(--ink);font-size:8.3px}
.tile-journey .tile-head{font-size:16px}
.tile-icon{position:absolute;left:15px;bottom:18px}
</style>
</head>
<body>
<svg class="hidden-defs" aria-hidden="true">
  <defs>
    <symbol id="ic-context" viewBox="0 0 24 24"><path d="M6 19 C6 10 12 5 19 5 C19 13 14 18 6 19Z M6 19 L13 11" fill="none" stroke="#fff" stroke-width="2" stroke-linecap="round"/></symbol>
    <symbol id="ic-complex" viewBox="0 0 24 24"><path d="M7 5 H15 A3 3 0 0 1 15 11 H9 A3 3 0 0 0 9 17 H17" fill="none" stroke="#fff" stroke-width="2" stroke-linecap="round"/></symbol>
    <symbol id="ic-community" viewBox="0 0 24 24"><g fill="#fff"><circle cx="12" cy="8" r="3"/><circle cx="6" cy="10" r="2.3"/><circle cx="18" cy="10" r="2.3"/><rect x="8" y="12" width="8" height="7" rx="3"/><rect x="2.5" y="13.5" width="6" height="5.5" rx="2.5"/><rect x="15.5" y="13.5" width="6" height="5.5" rx="2.5"/></g></symbol>
    <symbol id="ic-coordinate" viewBox="0 0 24 24"><g fill="#fff"><rect x="5" y="5" width="6" height="6" rx="1"/><rect x="13" y="5" width="6" height="6" rx="1"/><rect x="5" y="13" width="6" height="6" rx="1"/><rect x="13" y="13" width="6" height="6" rx="1"/></g></symbol>
    <symbol id="ic-communicate" viewBox="0 0 24 24"><path d="M4 6 H15 V13 H9 L6 16 V13 H4Z" fill="#fff"/><path d="M17 9 H20 V16 H18 V18.5 L15.5 16 H11 V15" fill="none" stroke="#fff" stroke-width="1.6"/></symbol>
    <symbol id="ic-capacity" viewBox="0 0 24 24"><path d="M12 19 V6 M7 11 L12 6 L17 11" fill="none" stroke="#fff" stroke-width="2.2" stroke-linecap="round" stroke-linejoin="round"/></symbol>
    <symbol id="ic-group" viewBox="0 0 40 30"><g fill="currentColor"><circle cx="20" cy="7" r="5.5"/><circle cx="8" cy="10" r="4"/><circle cx="32" cy="10" r="4"/><rect x="13" y="14" width="14" height="14" rx="6"/><rect x="2" y="16" width="11" height="12" rx="5"/><rect x="27" y="16" width="11" height="12" rx="5"/></g></symbol>
  </defs>
</svg>

<main class="canvas">
  <p class="section-label" style="left:23px;top:12px">A4 BROCHURE<small>SIDE A</small></p>
  <p class="section-label" style="left:584px;top:28px">A3 POSTER</p>
  <p class="section-label" style="left:960px;top:28px">PULL-UP BANNER</p>
  <p class="section-label" style="left:20px;top:534px">SOCIAL MEDIA TILES (1080 x 1080px)</p>

  <!-- A4 brochure, side A -->
  <section class="piece brochure" aria-label="A4 brochure side A">
    <div class="panel panel-cover">
      <p class="kicker">Harbourline Charter for</p>
      <h1 class="cover-title"><span class="title-a" style="display:block">Community</span><span class="title-b" style="display:block">Mending</span></h1>
      <p class="cover-tagline">Guiding our shared efforts for stronger, more resilient communities.</p>
      <div class="art" role="img" aria-label="Illustrated wattle branch with gum leaves" style="left:90px;top:190px;width:110px;height:250px;background:radial-gradient(ellipse at 55% 50%,#4d6e3c 0%,#2f5a3c 45%,rgba(14,58,56,0) 75%)"></div>
      <svg class="art" style="left:0;top:330px" width="197" height="70" viewBox="0 0 197 70" aria-hidden="true"><path d="M0 30 C50 20 90 30 120 50 S180 70 197 60" fill="none" stroke="#f0f0f0" stroke-width="2" stroke-dasharray="2 4"/><path d="M0 36 C50 26 90 36 120 56" fill="none" stroke="#e0662a" stroke-width="1" stroke-dasharray="1 3"/></svg>
      <p class="cover-values">People.<br>Partnership.<br>Resilience.</p>
    </div>
    <div class="panel panel-partners">
      <p class="partners-heading">Partners in<br>development</p>
      <div class="partner-list">
        <div class="partner wide"><span class="partner-mark"></span>Tidewater Commonwealth Home Office</div>
        <div class="partner wide"><span class="partner-mark"></span>Tidewater Legal Services Office</div>
        <div class="partner wide"><span class="partner-mark"></span>Tidewater Social Care Office</div>
        <div class="partner wide"><span class="partner-mark"></span>Harbour Aid Society</div>
        <div class="partner"><span class="partner-mark"></span>Southcape Isle Council</div>
        <div class="partner"><span class="partner-mark square"></span>Greenvale State</div>
        <div class="partner"><span class="partner-mark"></span>Capital Shire</div>
        <div class="partner"><span class="partner-mark"></span>Topend Region</div>
        <div class="partner"><span class="partner-mark"></span>Sunreef State</div>
        <div class="partner"><span class="partner-mark"></span>Saltbush State</div>
        <div class="partner"></div>
        <div class="partner"><span class="partner-mark square"></span>Eastcoast State</div>
        <div class="partner wide"><span class="partner-mark"></span>Community Mending Reference Circle</div>
      </div>
      <svg class="art" style="left:0;bottom:0" width="155" height="40" viewBox="0 0 155 40" aria-hidden="true"><path d="M60 40 C90 18 130 14 155 20 V40Z" fill="#2f5a3c"/></svg>
    </div>
    <div class="panel panel-overview">
      <p class="overview-text">The Harbourline Charter for Community Mending provide a nationally agreed framework to guide recovery policy and practice across Australia.</p>
      <p class="overview-text">The Principles support recovery practitioners, governments, non-government organisations and communities to deliver effective, community-centred recovery outcomes.</p>
      <p class="overview-heading">SUCCESSFUL RECOVERY</p>
      <div class="principle-row"><svg class="dot" viewBox="0 0 22 22"><circle cx="11" cy="11" r="11" fill="var(--c-context)"/><use href="#ic-context" x="4" y="4" width="14" height="14"/></svg><div><strong>Understand CONTEXT</strong><span>Grounded in local knowledge, values and strengths.</span></div></div>
      <div class="principle-row"><svg class="dot" viewBox="0 0 22 22"><circle cx="11" cy="11" r="11" fill="var(--c-complex)"/><use href="#ic-complex" x="4" y="4" width="14" height="14"/></svg><div><strong>Recognise COMPLEXITY</strong><span>Responsive to change and multiple, evolving impacts.</span></div></div>
      <div class="principle-row"><svg class="dot" viewBox="0 0 22 22"><circle cx="11" cy="11" r="11" fill="var(--c-community)"/><use href="#ic-community" x="4" y="4" width="14" height="14"/></svg><div><strong>Use COMMUNITY-CENTRED approaches</strong><span>Empowering communities to lead their recovery.</span></div></div>
      <div class="principle-row"><svg class="dot" viewBox="0 0 22 22"><circle cx="11" cy="11" r="11" fill="var(--c-coordinate)"/><use href="#ic-coordinate" x="4" y="4" width="14" height="14"/></svg><div><strong>COORDINATE all activities</strong><span>Working together with shared purpose and planning.</span></div></div>
      <div class="principle-row"><svg class="dot" viewBox="0 0 22 22"><circle cx="11" cy="11" r="11" fill="var(--c-communicate)"/><use href="#ic-communicate" x="4" y="4" width="14" height="14"/></svg><div><strong>COMMUNICATE effectively</strong><span>Clear, inclusive and respectful two-way communication.</span></div></div>
      <div class="principle-row"><svg class="dot" viewBox="0 0 22 22"><circle cx="11" cy="11" r="11" fill="var(--c-capacity)"/><use href="#ic-capacity" x="4" y="4" width="14" height="14"/></svg><div><strong>Recognise and build CAPACITY</strong><span>Building skills, capability and long-term resilience.</span></div></div>
      <div class="art" role="img" aria-label="Illustrated eucalyptus sprig" style="right:0;bottom:0;width:110px;height:70px;background:radial-gradient(ellipse at 70% 80%,#5f7f45 0%,rgba(14,58,56,0) 70%)"></div>
    </div>
  </section>

  <!-- A3 poster -->
  <section class="piece poster" aria-label="A3 poster">
    <div class="art" role="img" aria-label="Illustrated gum leaves and wattle framing the top corners" style="left:0;top:0;width:365px;height:90px;background:radial-gradient(ellipse at 5% 10%,#6f8f55 0%,rgba(246,240,226,0) 45%),radial-gradient(ellipse at 90% 5%,#3f6b4c 0%,#e3c45c 25%,rgba(246,240,226,0) 50%)"></div>
    <div class="poster-title">
      <p class="kicker">Harbourline Charter for</p>
      <p class="title-a">Community</p>
      <p class="title-b">Mending</p>
    </div>
    <p class="poster-tagline">Guiding our shared efforts for<br>stronger, more resilient communities.</p>
    <svg class="poster-diagram" width="300" height="282" viewBox="0 0 300 282" aria-label="Six principles arranged around a community">
      <g font-family="Figtree, sans-serif" font-size="9" fill="#fff" text-anchor="middle">
        <circle cx="100" cy="50" r="48" fill="var(--c-context)"/><use href="#ic-context" x="86" y="20" width="28" height="28"/><text x="100" y="64">Understand</text><text x="100" y="76">CONTEXT</text>
        <circle cx="200" cy="50" r="48" fill="var(--c-complex)"/><use href="#ic-complex" x="186" y="20" width="28" height="28"/><text x="200" y="64">Recognise</text><text x="200" y="76">COMPLEXITY</text>
        <circle cx="49" cy="141" r="48" fill="var(--c-community)"/><use href="#ic-community" x="37" y="109" width="24" height="24"/><text x="49" y="145">Use</text><text x="49" y="156" font-size="7.8">COMMUNITY-CENTRED</text><text x="49" y="167" font-size="8">approaches</text>
        <circle cx="251" cy="141" r="48" fill="var(--c-coordinate)"/><use href="#ic-coordinate" x="239" y="109" width="24" height="24"/><text x="251" y="151">COORDINATE</text><text x="251" y="163">all activities</text>
        <circle cx="100" cy="232" r="48" fill="var(--c-communicate)"/><use href="#ic-communicate" x="86" y="196" width="28" height="28"/><text x="100" y="238">COMMUNICATE</text><text x="100" y="250">effectively</text>
        <circle cx="200" cy="232" r="48" fill="var(--c-capacity)"/><use href="#ic-capacity" x="186" y="196" width="28" height="28"/><text x="200" y="238" font-size="8.5">Recognise and build</text><text x="200" y="250">CAPACITY</text>
        <circle cx="150" cy="141" r="50" fill="var(--cream)"/>
        <use href="#ic-group" x="122" y="120" width="56" height="42" style="color:var(--ink)"/>
      </g>
    </svg>
    <p class="poster-values"><i style="color:var(--c-communicate)">•</i>People <i style="color:var(--c-capacity)">•</i>Partnership <i style="color:var(--c-context)">•</i>Resilience</p>
    <svg class="poster-wave" viewBox="0 0 365 80" preserveAspectRatio="none" aria-hidden="true"><path d="M0 20 C80 0 150 30 230 22 S330 10 365 14 V80 H0Z" fill="#6f9a6a"/><path d="M0 28 C80 12 160 40 240 30 S330 20 365 24 V80 H0Z" fill="var(--forest)"/></svg>
    <p class="poster-sign">Stronger together. <span style="color:var(--c-capacity)">•</span>Ready for tomorrow.</p>
  </section>

  <!-- Pull-up banner -->
  <section class="piece banner" aria-label="Pull-up banner">
    <div class="banner-head">
      <p class="kicker">Harbourline Charter for</p>
      <p class="title-a" style="margin-top:6px">Community</p>
      <p class="title-b">Mending</p>
      <p class="banner-tagline">Guiding our shared efforts for stronger, more resilient communities.</p>
    </div>
    <svg class="art" style="left:0;top:205px" width="215" height="45" viewBox="0 0 215 45" aria-hidden="true"><path d="M0 20 C60 0 120 40 215 18 V45 H0Z" fill="var(--cream)"/><path d="M20 18 C70 4 110 30 150 20" fill="none" stroke="#fff" stroke-width="2" stroke-dasharray="2 4"/></svg>
    <div class="banner-list">
      <div class="banner-item"><svg width="36" height="36" viewBox="0 0 36 36"><circle cx="18" cy="18" r="18" fill="var(--c-context)"/><use href="#ic-context" x="8" y="8" width="20" height="20"/></svg><p>Understand<br><b>CONTEXT</b></p></div>
      <div class="banner-item"><svg width="36" height="36" viewBox="0 0 36 36"><circle cx="18" cy="18" r="18" fill="var(--c-complex)"/><use href="#ic-complex" x="8" y="8" width="20" height="20"/></svg><p>Recognise<br><b>COMPLEXITY</b></p></div>
      <div class="banner-item"><svg width="36" height="36" viewBox="0 0 36 36"><circle cx="18" cy="18" r="18" fill="var(--c-community)"/><use href="#ic-community" x="8" y="8" width="20" height="20"/></svg><p>Use<br><b>COMMUNITY-CENTRED</b><br>approaches</p></div>
      <div class="banner-item"><svg width="36" height="36" viewBox="0 0 36 36"><circle cx="18" cy="18" r="18" fill="var(--c-coordinate)"/><use href="#ic-coordinate" x="8" y="8" width="20" height="20"/></svg><p><b>COORDINATE</b><br>all activities</p></div>
      <div class="banner-item"><svg width="36" height="36" viewBox="0 0 36 36"><circle cx="18" cy="18" r="18" fill="var(--c-communicate)"/><use href="#ic-communicate" x="8" y="8" width="20" height="20"/></svg><p><b>COMMUNICATE</b><br>effectively</p></div>
      <div class="banner-item"><svg width="36" height="36" viewBox="0 0 36 36"><circle cx="18" cy="18" r="18" fill="var(--c-capacity)"/><use href="#ic-capacity" x="8" y="8" width="20" height="20"/></svg><p>Recognise and build<br><b>CAPACITY</b></p></div>
    </div>
    <div class="art" role="img" aria-label="Illustrated wattle sprig rising from the lower right" style="right:0;top:490px;width:80px;height:90px;background:radial-gradient(ellipse at 75% 60%,#8aa764 0%,#d9b94a 30%,rgba(246,240,226,0) 70%)"></div>
    <svg class="art" style="left:0;bottom:115px" width="215" height="40" viewBox="0 0 215 40" aria-hidden="true"><path d="M0 30 C70 10 140 40 215 5 V40 H0Z" fill="var(--navy)"/></svg>
    <div class="banner-foot">
      <p class="values">People. Partnership. Resilience.</p>
      <p class="sign">Stronger together.<br>Ready for tomorrow.</p>
    </div>
  </section>

  <!-- Social tiles -->
  <section class="piece tile tile-people" aria-label="Social tile: people and communities">
    <p class="tile-head">Recovery is<br>about people<br>and communities.</p>
    <p class="tile-body">Together we build<br>stronger, more<br>resilient futures.</p>
    <div class="art" role="img" aria-label="Illustrated wattle branch" style="right:0;top:60px;width:70px;height:150px;background:radial-gradient(ellipse at 60% 55%,#b59a35 0%,#3f6243 35%,rgba(14,58,56,0) 70%)"></div>
    <svg class="tile-icon" width="44" height="33" viewBox="0 0 40 30" style="color:var(--c-context)"><use href="#ic-group"/></svg>
  </section>

  <section class="piece tile tile-guide" aria-label="Social tile: guided by six principles">
    <div class="art" role="img" aria-label="Warm sun glow with dotted lines" style="right:0;top:0;width:90px;height:60px;background:radial-gradient(circle at 80% 10%,#f0cf6b 0%,rgba(246,240,226,0) 70%)"></div>
    <p class="tile-head">Guided by<br><span>6 Principles</span></p>
    <p class="tile-body">A shared framework for effective, inclusive and long-term recovery.</p>
    <svg class="art" style="left:104px;top:100px" width="76" height="80" viewBox="0 0 76 80" aria-label="Six principles around a community">
      <circle cx="38" cy="40" r="14" fill="var(--cream)"/><use href="#ic-group" x="27" y="33" width="22" height="16" style="color:var(--ink)"/>
      <circle cx="38" cy="10" r="9" fill="var(--c-context)"/>
      <circle cx="64" cy="25" r="9" fill="var(--c-complex)"/>
      <circle cx="64" cy="55" r="9" fill="var(--c-capacity)"/>
      <circle cx="38" cy="70" r="9" fill="var(--c-communicate)"/>
      <circle cx="12" cy="55" r="9" fill="var(--c-community)"/>
      <circle cx="12" cy="25" r="9" fill="var(--c-coordinate)"/>
    </svg>
    <svg class="art" style="left:0;bottom:0" width="182" height="40" viewBox="0 0 182 40" aria-hidden="true"><path d="M0 15 C50 0 110 30 182 10 V40 H0Z" fill="#f2b23d"/><path d="M0 25 C60 12 120 40 182 22 V40 H0Z" fill="var(--c-community)"/></svg>
  </section>

  <section class="piece tile tile-journey" aria-label="Social tile: local knowledge">
    <p class="tile-head">Local knowledge.<br>Shared leadership.<br>Lasting impact.</p>
    <p class="tile-body">Recovery is a<br>journey we take<br>together.</p>
    <div class="art" role="img" aria-label="Illustrated gum leaves" style="right:0;top:100px;width:70px;height:115px;background:radial-gradient(ellipse at 55% 60%,#7c9a74 0%,rgba(12,44,68,0) 70%)"></div>
    <svg class="art" style="left:0;bottom:0" width="170" height="40" viewBox="0 0 170 40" aria-hidden="true"><path d="M0 25 C60 10 110 35 170 15 V40 H0Z" fill="#1d5a7a"/></svg>
    <svg class="tile-icon" width="40" height="30" viewBox="0 0 40 30" style="color:var(--c-context)"><use href="#ic-group"/></svg>
  </section>
</main>
</body>
</html>
```